Create a premium soap bar box bar design for an all-natural, men's skincare brand.

We are launching a men’s premium, natural soap bar and skincare business. To start, we will be launching cold-press, all-natural soap bars with a few additional products such as lotions. We plan to expand our line into additional skincare products such as face exfoliants, moisturizers and cleansers that target basic needs such as anti-aging, clarifying and hydrating.

Our target audience is men ages 25-50, with a secondary audience of male teens. Our target audience are mid to high income, professionals that live in more urban areas, but enjoy being active outdoors after work and on the weekends. Our target audience are hard workers, humble and want to enjoy all that life has to offer – whether that’s on top of a mountain or an ocean wave. They hike, bike, skateboard, surf or any other sport that gets them outside. They are husbands, brothers and fathers – there for their family and friends.

Our brand is sophisticated, adventurous and has a sense of humor. Many of our competitors either focus on the rugged outdoors or are more pretentious. We are in-between. We are free spirited and love the fresh air. Our products are trustworthy with no toxic chemicals or harsh ingredients. We are all-natural and provide high-quality, premium products that our audience expects and deserves.

Target Market(s)

Men, ages 25-54 who are high-earning professionals, yet enjoy getting outdoors and being active on the weekends - hiking, biking, surfing, skateboarding and more.

Industry/Entity Type

Men's skincare

Font styles to use
Sans Serif

Requirements
Must have
• See attachments
Nice to have
• We would prefer to a have a premium, slightly more modern looking design that will appeal to our target audience and slightly higher price point.
Should not have
• Please do not include an icon for the fragrance, i.e. cinnamon sticks. However, we do need some differentiation for the fragrance, i.e. color, etc. as it will be on the shelf with other fragrances.

```html
<!DOCTYPE html>
<html lang="en">
<head>
<meta charset="utf-8">
<title>Ridge Harbor – Cinnamon Bark Soap Box</title>
<link href="https://fonts.googleapis.com/css2?family=Josefin+Sans:wght@300;400;600&family=Montserrat:wght@500;700;800&display=swap" rel="stylesheet">
<style>
  :root {
    --backdrop: #f2f2f2;
    --kraft: #c49a6a;
    --kraft-light: #d0aa7c;
    --kraft-dark: #b38959;
    --navy: #16293f;
    --navy-light: #1f3650;
    --red: #e64545;
    --white: #ffffff;
  }
  * { margin: 0; padding: 0; box-sizing: border-box; }
  html, body { width: 1200px; height: 675px; overflow: hidden; background: var(--backdrop); }
  .canvas { position: relative; width: 1200px; height: 675px; display: flex; justify-content: center; align-items: center; }
  .box { display: flex; box-shadow: 0 20px 40px rgba(0,0,0,.12); }

  .front {
    position: relative; width: 480px; height: 560px; overflow: hidden;
    background:
      radial-gradient(circle at 25% 30%, rgba(255,255,255,.10), transparent 45%),
      radial-gradient(circle at 80% 60%, rgba(0,0,0,.07), transparent 50%),
      linear-gradient(160deg, var(--kraft-light), var(--kraft) 50%, var(--kraft-dark));
  }
  .top-band { height: 72px; background: var(--red); display: flex; justify-content: center; align-items: center; }
  .brand-small { font-family: "Josefin Sans", sans-serif; font-weight: 600; color: var(--white); font-size: 18px; letter-spacing: 4px; text-transform: uppercase; }

  .category { margin-top: 30px; text-align: center; font-family: "Montserrat", sans-serif; font-weight: 700; font-size: 19px; letter-spacing: 5px; color: var(--white); text-transform: uppercase; }

  .lockup { margin-top: 32px; display: flex; justify-content: center; align-items: center; gap: 14px; }
  .lockup-circle { flex: none; width: 64px; height: 64px; border: 4px solid var(--navy); border-radius: 50%; }
  .lockup-text { display: flex; flex-direction: column; }
  .brand-name { font-family: "Josefin Sans", sans-serif; font-weight: 400; font-size: 40px; line-height: 1; color: var(--navy); letter-spacing: 1px; text-transform: uppercase; white-space: nowrap; }
  .tagline { font-family: "Josefin Sans", sans-serif; font-size: 12px; letter-spacing: 9px; color: var(--red); text-transform: uppercase; margin-top: 6px; }

  .scent { margin-top: 40px; text-align: center; }
  .scent-name { font-family: "Montserrat", sans-serif; font-weight: 800; font-size: 38px; line-height: 1.1; color: var(--navy); letter-spacing: 1px; text-transform: uppercase; }
  .scent-note { font-family: "Josefin Sans", sans-serif; font-weight: 300; font-size: 15px; letter-spacing: 8px; color: var(--navy); text-transform: uppercase; margin-top: 4px; }

  .shore-scene { position: absolute; left: 0; bottom: 0; width: 480px; height: 190px; }

  .details { position: absolute; left: 0; right: 0; bottom: 34px; display: flex; justify-content: center; align-items: center; gap: 18px; font-family: "Montserrat", sans-serif; color: var(--white); }
  .size { font-weight: 700; font-size: 17px; }
  .divider { width: 2px; height: 28px; background: var(--white); }
  .grit { font-weight: 700; font-size: 16px; letter-spacing: 2px; text-transform: uppercase; }

  .side { position: relative; width: 150px; height: 560px; background: var(--navy); overflow: hidden; }
  .side-dot { width: 16px; height: 16px; border: 2px solid var(--white); border-radius: 50%; }
  .side-copy { position: absolute; left: 0; top: 72px; width: 150px; height: 488px; display: flex; justify-content: center; align-items: center; }
  .side-copy-inner { transform: rotate(-90deg); white-space: nowrap; display: flex; flex-direction: column; gap: 6px; }
  .side-line { font-family: "Montserrat", sans-serif; font-weight: 500; font-size: 16px; color: var(--white); }
  .side-url { font-family: "Montserrat", sans-serif; font-weight: 800; font-size: 30px; color: var(--white); line-height: 1; }
  .directions { display: inline-flex; border: 1.5px solid var(--white); font-family: "Montserrat", sans-serif; font-size: 10px; color: var(--white); margin-top: 6px; align-self: flex-start; }
  .directions b { background: var(--white); color: var(--navy); padding: 3px 6px; letter-spacing: 1px; }
  .directions span { padding: 3px 10px; }
</style>
</head>
<body>
<div class="canvas">
  <div class="box">
    <section class="front">
      <header class="top-band"><span class="brand-small">Ridge Harbor</span></header>
      <p class="category">Men’s Natural Soap</p>
      <div class="lockup">
        <div class="lockup-circle"></div>
        <div class="lockup-text">
          <span class="brand-name">Ridge Harbor</span>
          <span class="tagline">Real Skincare</span>
        </div>
      </div>
      <div class="scent">
        <h1 class="scent-name">Cinnamon Bark</h1>
        <p class="scent-note">Sweet &amp; Spicy</p>
      </div>
      <svg class="shore-scene" viewBox="0 0 480 190" preserveAspectRatio="none" role="img" aria-label="Illustration of rolling ocean waves with a lighthouse on the shore">
        <defs>
          <linearGradient id="shore-fill" x1="0" y1="0" x2="0" y2="1">
            <stop offset="0" stop-color="#16293f"/>
            <stop offset="0.5" stop-color="#1c324b"/>
            <stop offset="1" stop-color="#16293f"/>
          </linearGradient>
        </defs>
        <path d="M0 40 C120 0 200 10 300 40 C380 64 430 40 480 30 L480 190 L0 190 Z" fill="url(#shore-fill)"/>
      </svg>
      <div class="details">
        <span class="size">5 Oz. Bar</span>
        <span class="divider"></span>
        <span class="grit">Medium Grit</span>
      </div>
    </section>
    <aside class="side">
      <div class="top-band"><span class="side-dot"></span></div>
      <div class="side-copy">
        <div class="side-copy-inner">
          <span class="side-line">Check out all our products at</span>
          <span class="side-url">ridgeharbor.com</span>
          <span class="directions"><b>DIRECTIONS:</b><span>Lather, rinse and repeat.</span></span>
        </div>
      </div>
    </aside>
  </div>
</div>
</body>
</html>
```